Flyer Design Project for Sports Medicine Services

I am a sports medicine doctor specialising in the diagnosis and management of sport and exercise injuries for all ages and levels of activity - from elite to weekend jogger. I work under the Business name Peak Stride Athletics and do have a company logo. I am wanting a flier that I can send to family doctors, physiotherapists and sports clubs explaining who I am what I can offer and why they should send me patients.
- I have a Masters in Sports Medicine (MSportsMed), Diplomas in Obstetrics/Gynaecology (DRANZCOG) and also Paediatrics (DCH) and certificate in advanced clinical hypnosis
-accurate diagnosis and management plan with their regular physio to return the player / athlete to the field / court /gym as soon as safely possible
-hypnosis for sports performance eg anxiety control, confidence and mental rehearsal for individuals and teams
- because there are many possible therapists and therapy options, as a sports doctor I can work out who they need to see a physiotherapist, surgeon, massage therapist chiropractor or podiatrist to return them to activity or whether cortisone, PRP or autologous blood injections are needed
-can provide one point of contact for coaches and clubs for rehabilitation and return to sport advice.
- work with Simon Drewett ex Australian Athlete, a Performance Strategist (NLB listed resource person) and registered Psychologist for best mental preparation for individuals teams and coach development
- can organise rapid access to MRI, ultrasound and specialist appointments if needed
-I work at 3 practices KinetaCare 518 Hollis Rd Hollis 84619027 Monday Wednesday Friday; Brackley Sports Clinic, 193 Brackley Rd, Adelaide 81946372 Tuesday Riverton Hawks Sports Medicine Clinic, Tolvane Arena 8162 5907 Thursday.
-facebook site peakstrideathletics
Updates
Hi All, just to clarify.. My name is Simon Drewett and I am the sports doctor. My wife is Simon Drewett and she is the psychologist. The flier should mainly be advertising my sports medicine services and a byline ( or at least not the first line in the title) about the Performance Strategy and Coach development.
Target Market(s)
family doctors (GPs), Sporting Clubs, Physiotherapists
Industry/Entity Type
Massage
Look and feel

```html
<!DOCTYPE html>
<html lang="en">
<head>
<meta charset="utf-8">
<title>Peak Stride Athletics – Sports Medicine Flyer</title>
<link rel="stylesheet" href="https://fonts.googleapis.com/css2?family=Lato:wght@400;700;900&family=Questrial&display=swap">
<style>
  :root {
    --ink: #000000;
    --sky: #29a8e0;
    --lime: #b3d334;
    --white: #ffffff;
    --footer-ink: #1a1a1a;
  }
  * { box-sizing: border-box; margin: 0; padding: 0; }
  html, body { width: 873px; height: 1200px; overflow: hidden; background: var(--ink); }
  .flyer {
    position: relative;
    width: 873px;
    height: 1200px;
    overflow: hidden;
    background: var(--ink);
    color: var(--white);
    font-family: "Lato", Arial, sans-serif;
  }
  .hero-image {
    position: absolute;
    left: 418px; top: 0;
    width: 455px; height: 428px;
    background:
      radial-gradient(ellipse 28% 40% at 55% 72%, rgba(220,30,60,0.85), rgba(220,30,60,0) 70%),
      radial-gradient(ellipse 60% 80% at 55% 45%, #2f6fd8 0%, #123a8a 45%, #050b1e 85%);
  }
  .brand-dot {
    position: absolute;
    left: 196px; top: 90px;
    width: 110px; height: 110px;
    border-radius: 50%;
    background: var(--sky);
  }
  .brand {
    position: absolute;
    left: 96px; top: 226px;
    width: 310px;
    color: var(--sky);
    font-weight: 900;
    font-size: 42px;
    line-height: 44px;
    letter-spacing: -1px;
    text-align: center;
  }
  .title-band {
    position: absolute;
    left: 0; top: 428px;
    width: 873px; height: 150px;
    background: var(--sky);
    display: flex; flex-direction: column; justify-content: center; align-items: center;
    text-align: center;
    padding-left: 30px;
  }
  .title-band h1 {
    font-family: Arial, "Lato", sans-serif;
    font-weight: 700;
    font-size: 44px;
    line-height: 52px;
  }
  .title-band .byline {
    font-family: Arial, "Lato", sans-serif;
    font-weight: 700;
    font-size: 25px;
    line-height: 34px;
    margin-top: 6px;
  }
  .intro {
    position: absolute;
    left: 109px; top: 632px;
    width: 671px;
    font-weight: 700;
    font-size: 23.5px;
    line-height: 30.4px;
    letter-spacing: 0.3px;
    text-align: justify;
    hyphens: auto;
  }
  .services {
    position: absolute;
    left: 99px; top: 805px;
    width: 668px;
    list-style: none;
    font-family: "Questrial", "Lato", sans-serif;
    font-size: 18.5px;
    line-height: 23.7px;
    letter-spacing: 0.4px;
  }
  .services li {
    position: relative;
    padding-left: 38px;
    margin-bottom: 23px;
    text-align: justify;
  }
  .services li::before {
    content: "";
    position: absolute;
    left: 4px; top: 7px;
    width: 12px; height: 12px;
    border-radius: 50%;
    background: var(--lime);
  }
  .clinics {
    position: absolute;
    left: 0; top: 1082px;
    width: 873px; height: 118px;
    background: var(--lime);
    color: var(--footer-ink);
    font-family: "Questrial", "Lato", sans-serif;
    font-size: 14.5px;
    line-height: 18.7px;
  }
  .clinic { position: absolute; top: 15px; }
  .clinic--one { left: 32px; }
  .clinic--two { left: 277px; }
  .clinic--three { left: 526px; }
  .clinic strong { font-family: "Lato", Arial, sans-serif; font-weight: 700; }
</style>
</head>
<body>
<div class="flyer">
  <div class="hero-image" role="img" aria-label="Illustration of a translucent blue human skeleton's back with the lower spine glowing red"></div>

  <div class="brand-dot"></div>
  <div class="brand">Peak Stride<br>Athletics</div>

  <div class="title-band">
    <h1>Sports Medicine &amp; Injury Management</h1>
    <p class="byline">with Elite Coach Development &amp; High Performance Psychology</p>
  </div>

  <p class="intro" lang="en">Simon Drewett a sports medicine doctor specialising in the diagnosis and management of sport and exercise injuries for all ages and levels of activity - from elite to weekend jogger.</p>

  <ul class="services">
    <li>I have a Masters in Sports Medicine (MSportsMed), Diplomas in Obstetrics/Gynaecology (DRANZCOG) and also Paediatrics (DCH) and certificate in advanced clinical hypnosis</li>
    <li>Accurate diagnosis and management plan with their regular physio to return the player / athlete to the field / court /gym as soon as safely possible</li>
    <li>Hypnosis for sports performance eg anxiety control, confidence and mental rehearsal for individuals and teams</li>
  </ul>

  <footer class="clinics">
    <div class="clinic clinic--one">Monday Wednesday Friday<br><strong>KinetaCare</strong><br>518 Hollis Rd Hollis<br><strong>84619027</strong></div>
    <div class="clinic clinic--two">Tuesday<br><strong>Brackley Sports Clinic</strong><br>193 Brackley Rd, Adelaide<br><strong>81946372</strong></div>
    <div class="clinic clinic--three">Thursday<br><strong>Riverton Hawks Sports Medicine Clinic</strong><br>Tolvane Arena<br><strong>8162 5907</strong></div>
  </footer>
</div>
</body>
</html>
```